Voltaryn - Web Design Project

I am looking for a 5 page design.
I would like it to be like the design of this site: www.quorvexlabs.com.
Which means it can be all one page effectively. With quick scroll tabs at the top.
I would like it to include parallax scrolling (The parallax effect uses multiple backgrounds which seem to move at different speeds to create a sensation of depth (creating a faux-3D effect)).
I have uploaded my logo. I would like this to be used in the site design.
I would like the site design to include 3D DNA creative.
Please note the Pixmora photos attached do not belong to me they are purely to inspire creative ideas. However I would be more than happy to purchase these photos to use if the designer thought this would be beneficial.
Requirements
Must have
- parallax scrolling
DNA pictures (3D effect)
Please use site for reference: www.quorvexlabs.com
Use at least 1 of the logos in design...

```html
<!DOCTYPE html>
<html lang="en">
<head>
<meta charset="utf-8">
<title>Voltaryn — Hybrid Advertising</title>
<link rel="stylesheet" href="https://fonts.googleapis.com/css2?family=Roboto+Condensed:wght@400;700&family=Roboto:wght@400&display=swap">
<style>
  :root{
    --white:#ffffff;
    --ink:#1d1f20;
    --nav:#4a4f52;
    --teal-light:#2bb0b6;
    --teal:#15949a;
    --teal-dark:#0b6f76;
    --rose-light:#c86a78;
    --rose:#b3505c;
    --rose-dark:#9a3f48;
    --green-light:#9fd27a;
    --green:#7fbf5d;
    --green-dark:#5d9a3e;
    --ring:#c4566a;
    --footer:#45b6dc;
    --social:#3d4448;
  }
  *{box-sizing:border-box;margin:0;padding:0}
  html,body{width:702px;height:1200px;overflow:hidden;background:var(--white)}
  body{font-family:"Roboto Condensed",Arial,sans-serif;position:relative}

  .site-header{position:absolute;left:0;top:0;width:702px;height:66px;background:var(--white)}
  .brand{position:absolute;left:70px;top:20px;display:flex;align-items:center;gap:7px}
  .brand-dot{width:16px;height:16px;border-radius:50%;background:var(--teal)}
  .brand-name{font-size:17px;font-weight:400;letter-spacing:2px;color:var(--nav);text-transform:uppercase}
  .main-nav{position:absolute;top:27px;left:0;width:702px;font-family:"Roboto",Arial,sans-serif;font-size:8px;color:var(--nav);text-transform:uppercase}
  .main-nav span{position:absolute;transform:translateX(-50%);white-space:nowrap}

  .band{position:absolute;left:0;width:702px;overflow:hidden}
  .band-bg{position:absolute;inset:0}
  .hero{top:66px;height:347px}
  .hero .band-bg{background:linear-gradient(100deg,var(--teal-light) 0%,var(--teal) 55%,var(--teal-dark) 100%)}
  .research{top:413px;height:353px}
  .research .band-bg{background:linear-gradient(100deg,var(--rose-dark) 0%,var(--rose-light) 50%,var(--rose) 100%)}
  .services{top:766px;height:354px}
  .services .band-bg{background:linear-gradient(100deg,var(--green-dark) 0%,var(--green-light) 45%,var(--green) 100%)}

  .copy{position:absolute;color:var(--white);text-transform:uppercase}
  .copy h1,.copy h2{font-weight:400;color:var(--ink);line-height:1;font-size:39px;text-shadow:0 1px 2px rgba(0,0,0,.25)}
  .copy h3{font-weight:400;font-size:27px;line-height:1;margin-top:8px;text-shadow:0 1px 2px rgba(0,0,0,.3)}
  .copy p{font-size:12.6px;line-height:16.2px;margin-top:15px;text-align:justify;text-shadow:0 1px 2px rgba(0,0,0,.35)}
  .hero .copy{left:76px;top:92px;width:265px}
  .hero .copy p{text-align:left;margin-top:22px}
  .research .copy{left:357px;top:94px;width:256px}
  .services .copy{left:368px;top:93px;width:256px}

  .slider-arrow{position:absolute;top:160px;width:20px;height:20px;border-radius:50%}
  .slider-arrow.prev{left:14px;background:rgba(0,0,0,.08)}
  .slider-arrow.next{left:670px;background:rgba(0,0,0,.35)}

  .feature-ring{position:absolute;left:70px;width:232px;height:232px;border-radius:50%;background:var(--white);border:5px solid var(--ring);box-shadow:0 3px 10px rgba(0,0,0,.35)}
  .research .feature-ring{top:68px}
  .services .feature-ring{top:68px}
  .feature-art{position:absolute;left:28px;top:28px;width:166px;height:166px;border-radius:50%}
  .research .feature-art{background:radial-gradient(circle at 45% 45%,#d8eefb 0%,#7cc2ec 60%,#3f8fd0 100%)}
  .services .feature-art{left:14px;top:14px;width:194px;height:194px;background:radial-gradient(circle,#fafafa 0%,#eeeeee 100%)}

  .site-footer{position:absolute;left:0;top:1120px;width:702px;height:80px;background:var(--footer)}
  .copyright{position:absolute;left:71px;top:38px;font-size:6.5px;color:var(--ink);text-transform:uppercase}
  .social{position:absolute;left:511px;top:32px;display:flex;gap:2.5px}
  .social span{width:18px;height:18px;border-radius:50%;background:var(--social)}
</style>
</head>
<body>
  <header class="site-header">
    <div class="brand"><span class="brand-dot"></span><span class="brand-name">Voltaryn</span></div>
    <nav class="main-nav">
      <span style="left:254px">Home</span>
      <span style="left:317px">Services</span>
      <span style="left:388px">Research</span>
      <span style="left:462px">Products</span>
      <span style="left:533px">Gallery</span>
      <span style="left:601px">Contact</span>
    </nav>
  </header>

  <section class="band hero">
    <div class="band-bg" role="img" aria-label="Glowing turquoise 3D DNA double helix on a teal background"></div>
    <span class="slider-arrow prev"></span>
    <span class="slider-arrow next"></span>
    <div class="copy">
      <h1>Voltaryn</h1>
      <h3>Hybrid Advertising</h3>
      <p>DNA research centre is an autonomous registered research organization, which provides services and training in biotechnology, bioinformatics, clinical research &amp; forensic science.</p>
    </div>
  </section>

  <section class="band research">
    <div class="band-bg" role="img" aria-label="Soft pink DNA strands over a rose background"></div>
    <div class="feature-ring">
      <div class="feature-art" role="img" aria-label="Microscope in front of blue chromosomes"></div>
    </div>
    <div class="copy">
      <h2>Research</h2>
      <h3>DNA Research Model</h3>
      <p>Perspiciatis unde omnis iste natus error sit voluptatem accusantium doloremque laudantium, totam rem aperiam, eaque ipsa quae ab illo inventore veritatis et quasi architecto beatae vitae dicta sunt explicabo.</p>
    </div>
  </section>

  <section class="band services">
    <div class="band-bg" role="img" aria-label="Green DNA helix with faint chemical structure formulas"></div>
    <div class="feature-ring">
      <div class="feature-art" role="img" aria-label="DNA helix illustration with a pipette and sample tube"></div>
    </div>
    <div class="copy">
      <h2>Services</h2>
      <h3>Perspiciatis Unde</h3>
      <p>Perspiciatis unde omnis iste natus error sit voluptatem accusantium doloremque laudantium, totam rem aperiam, eaque ipsa quae ab illo inventore veritatis et quasi architecto beatae vitae dicta sunt explicabo.</p>
    </div>
  </section>

  <footer class="site-footer">
    <p class="copyright">© 2012 Voltaryn.All rights reserved.</p>
    <div class="social"><span></span><span></span><span></span><span></span><span></span><span></span></div>
  </footer>
</body>
</html>
```